Hollendorf Business Card

This is the personal business card for Dr Mark Hollendorf and convers three area of his professional activity - all of them involve (foreign) languages:
o QRVB International Ltd - A translation company with 50 staff. Trades internationally
o WideHarbor Ltd - a global online auction marketplace for translation services (startup)
o Tonal Mosaic - cutting edge technology from the brain sciences which helps learners assimilate the sound patterns of a new language (startup)

Target Market(s)

The card needs to have a "cutting edge" feel - but for a fairly conservative audience - academics, investors.

Industry/Entity Type

Business

Requirements
Must have
• Text:
Dr Mark Hollendorf

Co-founder QRVB International Ltd (Language translation)
Founder WideHarbor Ltd (Translation marketplace)
Founder Tonal Mosaic (Language acquisition)

email: mark.oswin@velmora.co.nz
Phone: +64 21 596 3172
Chirper: @MarkOswin7

```html
<!DOCTYPE html>
<html lang="en">
<head>
<meta charset="utf-8">
<title>Hollendorf Business Card</title>
<link rel="stylesheet" href="https://fonts.googleapis.com/css2?family=Cinzel:wght@600&family=Sorts+Mill+Goudy&family=Jost:wght@400&display=swap">
<style>
  :root {
    --paper: #ffffff;
    --ink: #1a1a1a;
    --olive-dark: #6e7320;
    --olive-light: #c9cd7e;
    --olive: #9c9d1e;
  }
  html, body {
    margin: 0;
    padding: 0;
    width: 1200px;
    height: 686px;
    overflow: hidden;
    background: var(--paper);
  }
  .card {
    position: relative;
    width: 1200px;
    height: 686px;
    background: var(--paper);
    color: var(--ink);
  }
  .card__name {
    position: absolute;
    top: 58px;
    left: 0;
    width: 1200px;
    margin: 0;
    text-align: center;
    font-family: "Cinzel", serif;
    font-weight: 600;
    font-size: 44px;
    letter-spacing: 1px;
  }
  .card__bands {
    position: absolute;
    top: 137px;
    left: 42px;
    width: 1158px;
    height: 16px;
  }
  .ventures {
    position: absolute;
    top: 190px;
    left: 60px;
    width: 535px;
    margin: 0;
    padding: 0;
    list-style: none;
    text-align: center;
    font-family: "Sorts Mill Goudy", serif;
    font-size: 19px;
    line-height: 34px;
  }
  .ventures li { margin-bottom: 32px; }
  .contact {
    position: absolute;
    top: 425px;
    left: 60px;
    width: 535px;
    text-align: center;
    font-family: "Jost", sans-serif;
    font-size: 31px;
    line-height: 47px;
  }
  .contact p { margin: 0; }
  .profile {
    position: absolute;
    top: 318px;
    left: 650px;
    width: 520px;
    text-align: center;
    font-family: "Sorts Mill Goudy", serif;
  }
  .profile__name {
    margin: 0 0 30px;
    font-size: 26px;
    font-weight: bold;
  }
  .profile__field {
    margin: 0;
    font-size: 27px;
  }
</style>
</head>
<body>
<main class="card">
  <h1 class="card__name">Dr. Mark Hollendorf</h1>

  <svg class="card__bands" viewBox="0 0 1158 16" aria-hidden="true">
    <rect x="0" y="0" width="380" height="16" fill="var(--olive-dark)"/>
    <rect x="380" y="0" width="386" height="16" fill="var(--olive-light)"/>
    <rect x="766" y="0" width="392" height="16" fill="var(--olive)"/>
  </svg>

  <ul class="ventures">
    <li>Co-founder QRVB International Ltd (Language<br>Translation)</li>
    <li>Founder WideHarbor Ltd (Translation<br>Marketplace)</li>
    <li>Founder Tonal Mosaic (Language Acquisition)</li>
  </ul>

  <div class="contact">
    <p>Phone: +64 21 596 3172</p>
    <p>Chirper: @MarkOswin7</p>
    <p>E-mail: mark.oswin@velmora.co.nz</p>
  </div>

  <div class="profile">
    <p class="profile__name">Mark Hollendorf</p>
    <p class="profile__field">Profession in Foreign Languages</p>
  </div>
</main>
</body>
</html>
```